Vitamin B12 Liquid Drops Label

hi, i need a label designed for my vitamin b12 drops that i am going to be selling on shopzello. the label needs to quickly capture the attention of a buyer as he or she is scrolling through the thumbnail search results on shopzello.com my brand is called nralo. i already have an example brand logo i will be using, however, i need help designing the rest of the label. attached are some examples of labels i like for other supplements.some of these examples are pink. i do not want pink. please go for a blue/green color scheme. THE DESIGN MUST BE BOLD

Target Market(s)

adults ages 30 - 64

Font styles to use
Sans Serif

Colors
0455a3
cedeed
3176b5
85acd3
cfdeed
9bcb3b
abd037
cadf82
00a990

Requirements
Must have
• - bold design
• - somewhat gender-neutral color scheme because this will be used equally by men and women
• - B12 MUST be very prominent and visible on the label
Should not have
• - it should not be "crunchy" looking

```html
<!DOCTYPE html>
<html lang="en">
<head>
<meta charset="utf-8">
<title>Nralo Vitamin B12 Label</title>
<link rel="stylesheet" href="https://fonts.googleapis.com/css2?family=Antonio:wght@600;700&display=swap">
<style>
  :root {
    --backdrop-inner: #3a3a3a;
    --backdrop-outer: #161616;
    --label-green: #9bcb3b;
    --label-blue: #0455a3;
    --title-blue: #0455a3;
    --accent-light: #cadf82;
    --accent-pale: #cedeed;
  }
  html, body {
    margin: 0;
    padding: 0;
    width: 1200px;
    height: 900px;
    overflow: hidden;
  }
  body {
    background: radial-gradient(ellipse at 50% 45%, var(--backdrop-inner) 0%, var(--backdrop-outer) 80%);
    font-family: "Antonio", "Arial Narrow", sans-serif;
  }
  .label-panel {
    position: absolute;
    left: 400px;
    top: 30px;
    width: 400px;
    height: 840px;
    display: block;
  }
  .label-base { fill: var(--label-blue); }
  .label-green-field { fill: var(--label-green); }
  .product-title {
    fill: var(--title-blue);
    font-family: "Antonio", "Arial Narrow", sans-serif;
    font-weight: 700;
    font-size: 84px;
  }
  .ingredient-name {
    fill: var(--accent-light);
    font-family: "Antonio", "Arial Narrow", sans-serif;
    font-weight: 600;
    font-size: 26px;
  }
  .brand-name {
    fill: var(--accent-light);
    font-family: "Antonio", "Arial Narrow", sans-serif;
    font-weight: 700;
    font-size: 74px;
  }
</style>
</head>
<body>
  <svg class="label-panel" viewBox="0 0 400 840" xmlns="http://www.w3.org/2000/svg">
    <rect class="label-base" x="0" y="0" width="400" height="840"/>
    <polygon class="label-green-field" points="0,0 398,0 292,451 0,451"/>
    <text class="product-title" x="20" y="428" textLength="252" lengthAdjust="spacingAndGlyphs">VITAMIN B12</text>
    <text class="ingredient-name" x="22" y="522" textLength="252" lengthAdjust="spacing">METHYLCOBALAMIN</text>
    <text class="brand-name" x="372" y="784" text-anchor="end" textLength="160" lengthAdjust="spacingAndGlyphs">NRALO</text>
  </svg>
</body>
</html>
```